Electrician Business Card/ company logo/small business

New Business Cards and logo needed that will catch peoples eye and say we went that extra step. Attached is a design possibly to be incorporated, if u have your own great, lets see it!... This will be a small local business. thank you for all you do!
Halvern Electric
Ned Fosky Owner
Journeyman Electrician
phone 1.555.208.3471
email: KQLHalvernElectric@quellmail.net
call for free estimate!
Updates

Accepted and approved for cards

Target Market(s)

support small local business

Industry/Entity Type

Electrical,

Contact Information for Business Card

name, title,company/ logo, phone, email, free estimate

Other font styles liked:
• easy to read

Colors

Designer to choose colors to be used in the design.

Requirements
Must have
• eye catching everything! logo and halvern electric listed on business card/logo, incorp logo in the background of card
Nice to have
• lightening bolts in eyes or around the triangle? vertical, modern, any design that would be unique and stand out
Should not have
• pinks, reds, yellows,brown

```html
<!DOCTYPE html>
<html lang="en">
<head>
<meta charset="utf-8">
<title>Halvern Electric – Business Card</title>
<link rel="stylesheet" href="https://fonts.googleapis.com/css2?family=Archivo+Black&family=Arimo:wght@400;700&display=swap">
<style>
  :root {
    --page-bg: #e9ebee;
    --blue-deep: #0552ae;
    --blue-mid: #0a6cc4;
    --blue-bright: #0a92d6;
    --ink: #1d1f24;
    --white: #ffffff;
  }
  * { box-sizing: border-box; margin: 0; padding: 0; }
  html, body {
    width: 1200px; height: 900px; overflow: hidden;
    background: var(--page-bg);
  }
  .sheet {
    width: 1200px; height: 900px;
    display: flex; flex-direction: column; align-items: center; justify-content: center;
    gap: 40px;
  }
  .card {
    position: relative;
    width: 700px; height: 400px;
    overflow: hidden;
    box-shadow: 0 6px 18px rgba(0, 0, 0, 0.18);
  }

  /* Front */
  .card-front {
    background: linear-gradient(180deg, var(--blue-deep) 0%, var(--blue-mid) 45%, var(--blue-bright) 100%);
    display: flex; align-items: center; justify-content: center;
  }
  .brand {
    display: flex; align-items: center; gap: 18px;
    font-family: "Archivo Black", "Arial Black", sans-serif;
    text-transform: uppercase;
    letter-spacing: 1px;
    line-height: 1;
  }
  .brand-dot { border-radius: 50%; flex: none; }
  .card-front .brand { color: var(--white); font-size: 44px; }
  .card-front .brand-dot { width: 46px; height: 46px; background: var(--white); }

  /* Back */
  .card-back { background: var(--white); }
  .card-back .brand {
    position: absolute; top: 44px; right: 48px;
    flex-direction: column; gap: 12px;
    color: var(--blue-mid); font-size: 30px; text-align: center;
  }
  .card-back .brand-name { line-height: 1.05; }
  .card-back .brand-dot { width: 64px; height: 64px; background: var(--blue-mid); }

  .holder { position: absolute; left: 56px; top: 96px; }
  .holder-name {
    font-family: "Archivo Black", "Arial Black", sans-serif;
    font-size: 32px; color: var(--blue-mid); letter-spacing: 0.5px;
    line-height: 1;
  }
  .holder-title {
    font-family: "Arimo", Arial, sans-serif;
    font-size: 19px; color: var(--ink); margin-top: 4px;
  }

  .contact {
    position: absolute; left: 110px; top: 186px;
    font-family: "Arimo", Arial, sans-serif;
    font-size: 19px; color: var(--ink);
    list-style: none;
  }
  .contact li { display: flex; align-items: center; gap: 10px; line-height: 28px; }
  .contact svg { width: 18px; height: 18px; fill: var(--blue-mid); flex: none; }
  .contact .estimate {
    font-weight: 700; font-size: 16px; color: var(--blue-mid);
    padding-left: 28px;
  }

  .wave { position: absolute; inset: 0; width: 700px; height: 400px; }
  .wave-light { fill: var(--blue-bright); }
  .wave-deep { fill: var(--blue-deep); }

  .website {
    position: absolute; right: 40px; bottom: 50px;
    font-family: "Arimo", Arial, sans-serif;
    font-size: 17px; color: var(--white);
  }
</style>
</head>
<body>
<main class="sheet">

  <section class="card card-front" aria-label="Card front">
    <div class="brand">
      <span class="brand-dot"></span>
      <span class="brand-name">Halvern Electric</span>
    </div>
  </section>

  <section class="card card-back" aria-label="Card back">
    <svg class="wave" viewBox="0 0 700 400" aria-hidden="true">
      <path class="wave-light" d="M0,338 C240,352 460,318 640,248 C490,330 270,376 0,368 Z"/>
      <path class="wave-deep" d="M0,376 C280,382 490,320 700,214 L700,400 L0,400 Z"/>
    </svg>

    <div class="brand">
      <span class="brand-dot"></span>
      <span class="brand-name">Halvern<br>Electric</span>
    </div>

    <div class="holder">
      <p class="holder-name">NED FOSKY</p>
      <p class="holder-title">Journeyman Electrician</p>
    </div>

    <ul class="contact">
      <li>
        <svg viewBox="0 0 24 24" aria-hidden="true"><path d="M6.6 10.8a15.1 15.1 0 0 0 6.6 6.6l2.2-2.2a1 1 0 0 1 1-.25 11.4 11.4 0 0 0 3.6.57 1 1 0 0 1 1 1V20a1 1 0 0 1-1 1A17 17 0 0 1 3 4a1 1 0 0 1 1-1h3.5a1 1 0 0 1 1 1c0 1.25.2 2.45.57 3.57a1 1 0 0 1-.25 1z"/></svg>
        <span>1.555.208.3471</span>
      </li>
      <li>
        <svg viewBox="0 0 24 24" aria-hidden="true"><path d="M2 5h20v14H2z M2 5l10 8 10-8" fill="none" stroke="#0a6cc4" stroke-width="2"/></svg>
        <span>KQLHalvernElectric@quellmail.net</span>
      </li>
      <li class="estimate">Call for a free estimate!</li>
    </ul>

    <p class="website">www.halvernelectric.com</p>
  </section>

</main>
</body>
</html>
```